Landscape design build company door flyer

I would like this flyer to convey a high-level of professionalism for a company that is excellent with communication with their clients as well as a company that does incredible installations

Went on vacation/holiday

```html
<!DOCTYPE html>
<html lang="en">
<head>
<meta charset="utf-8">
<title>Cedarline Builders – Outdoor Living Spaces Flyer</title>
<link rel="stylesheet" href="https://fonts.googleapis.com/css2?family=Montserrat:wght@400;500;600;700;800&display=swap">
<style>
  :root{
    --navy:#163349;
    --navy-deep:#0f2638;
    --navy-glow:#2a5878;
    --ink:#1c2f3f;
    --rule-grey:#b9bec3;
    --paper:#ffffff;
    --backdrop:#e6e6e6;
  }
  *{margin:0;padding:0;box-sizing:border-box}
  html,body{width:1200px;height:1029px;overflow:hidden;background:var(--backdrop);font-family:"Montserrat",sans-serif}
  .flyer{position:absolute;left:216px;top:20px;width:768px;height:989px;background:var(--paper);box-shadow:0 6px 24px rgba(0,0,0,.12);overflow:hidden}
  .info-column{position:absolute;left:0;top:0;width:329px;height:989px}
  .brand{position:absolute;left:0;top:128px;width:329px;text-align:center;color:var(--navy)}
  .brand-mark{display:block;width:12px;height:12px;border-radius:50%;background:var(--navy);margin:0 auto 6px}
  .brand-name{font-weight:700;font-size:16px;letter-spacing:.2px;line-height:1}
  .brand-tag{font-weight:700;font-size:6.6px;margin-top:3px;letter-spacing:.1px}
  .headline{position:absolute;left:38px;top:184px;font-weight:800;font-size:35px;line-height:36.6px;color:var(--navy);letter-spacing:-.3px}
  .divider{position:absolute;left:39px;top:348px;width:256px;height:2px;background:var(--rule-grey)}
  .divider::before{content:"";position:absolute;left:0;top:-.5px;width:124px;height:3px;background:var(--navy)}
  .intro{position:absolute;left:39px;top:364px;width:258px;font-size:11.6px;line-height:14.7px;color:var(--ink);text-align:justify;letter-spacing:.15px}
  .services{position:absolute;left:39px;top:471px;list-style:none}
  .services li{position:relative;height:34.2px;padding-left:10px;font-weight:700;font-size:15.6px;color:var(--navy);line-height:24px}
  .services li::before{content:"";position:absolute;left:0;top:2px;width:2px;height:20px;background:var(--navy)}
  .contact-panel{position:absolute;left:0;top:720px;width:329px;height:269px;color:#fff;
    background:radial-gradient(ellipse 70% 60% at 45% 72%,var(--navy-glow) 0%,var(--navy) 55%,var(--navy-deep) 100%)}
  .areas{position:absolute;left:39px;top:17px;width:260px;font-size:12.2px;line-height:18.2px;font-weight:400;letter-spacing:.1px}
  .areas b{font-weight:700}
  .contact-label{position:absolute;left:39px;top:106px;height:22px;width:168px;background:#fff;color:var(--navy);
    font-weight:700;font-size:15.6px;letter-spacing:4.4px;line-height:22px;padding-left:8px;
    clip-path:polygon(0 0,92% 0,100% 50%,92% 100%,0 100%)}
  .contact-line{position:absolute;left:206px;top:116.5px;width:82px;height:1px;background:#c9d3db}
  .phone{position:absolute;left:39px;top:144px;display:flex;align-items:center;gap:14px}
  .phone svg{width:21px;height:23px}
  .phone-number{font-weight:700;font-size:25.5px;letter-spacing:3.6px}
  .detail{position:absolute;left:42px;display:flex;align-items:center;gap:16px;font-size:12.2px;letter-spacing:.3px}
  .detail svg{width:15px;height:15px}
  .detail.email{top:180px}
  .detail.web{top:202px}
  .gallery{position:absolute;left:332px;top:0;width:436px;height:989px;display:grid;grid-template-rows:repeat(4,1fr);row-gap:3px}
  .photo{width:100%;height:100%}
  .photo-deck{background:linear-gradient(180deg,#4f7a3a 0%,#7a9c55 28%,#9b5a36 52%,#a4603a 78%,#6e3d24 100%)}
  .photo-aerial{background:linear-gradient(135deg,#2f4a2a 0%,#6f7a78 35%,#8a8d90 55%,#5a3f2c 75%,#3f5a32 100%)}
  .photo-pool{background:linear-gradient(180deg,#b98a63 0%,#eef1f0 30%,#d8dedd 50%,#4fbfb2 72%,#7fd6c9 100%)}
  .photo-pavilion{background:linear-gradient(180deg,#c08a5a 0%,#3a3f45 30%,#6f6b66 55%,#8c8884 75%,#43505e 100%)}
</style>
</head>
<body>
<main class="flyer">
  <section class="info-column">
    <header class="brand">
      <span class="brand-mark"></span>
      <div class="brand-name">CEDARLINE BUILDERS</div>
      <div class="brand-tag">OUTDOOR LIVING SPACES</div>
    </header>

    <h1 class="headline">LET’S CREATE<br>YOUR DREAM<br>OUTDOOR<br>LIVING SPACE!</h1>
    <div class="divider"></div>

    <p class="intro">Discover the endless possibilities for your outdoor space with The Cedarline Builders Team. Our team of skilled artisans is dedicated to turning your outdoor space into a breathtaking oasis that you’ll love coming home to. Our services include:</p>

    <ul class="services">
      <li>PAVER PATIOS</li>
      <li>PAVER DRIVEWAYS</li>
      <li>RETAINING WALLS</li>
      <li>DECKS &amp; RAILINGS</li>
      <li>POOLS</li>
      <li>OUTDOOR LIGHTING</li>
      <li>FIREPITS &amp; FIREPLACES</li>
    </ul>

    <footer class="contact-panel">
      <p class="areas">Our service areas include <b>Bellevue, Issaquah, Kirkland, Redmond, and Sammamish</b>. We are trusted, tested and reliable with over 20-years experiences.</p>
      <div class="contact-label">CONTACT US</div>
      <div class="contact-line"></div>
      <div class="phone">
        <svg viewBox="0 0 24 24" aria-hidden="true"><path fill="#fff" d="M6.6 10.8a15.2 15.2 0 0 0 6.6 6.6l2.2-2.2a1 1 0 0 1 1-.25 11.4 11.4 0 0 0 3.6.57 1 1 0 0 1 1 1V20a1 1 0 0 1-1 1A17 17 0 0 1 3 4a1 1 0 0 1 1-1h3.5a1 1 0 0 1 1 1c0 1.25.2 2.45.57 3.6a1 1 0 0 1-.25 1z"/></svg>
        <span class="phone-number">206-555-0148</span>
      </div>
      <div class="detail email">
        <svg viewBox="0 0 16 16" aria-hidden="true"><rect x="1" y="3" width="14" height="10" fill="#fff"/><path d="M1.5 3.5 8 8.5l6.5-5" fill="none" stroke="#163349" stroke-width="1.3"/></svg>
        <span>info@cedarlinebuilders.com</span>
      </div>
      <div class="detail web">
        <svg viewBox="0 0 16 16" aria-hidden="true" fill="none" stroke="#fff" stroke-width="1"><circle cx="8" cy="8" r="6.5"/><ellipse cx="8" cy="8" rx="3" ry="6.5"/><path d="M1.5 8h13M2.5 4.8h11M2.5 11.2h11"/></svg>
        <span>www.cedarlinebuilders.com</span>
      </div>
    </footer>
  </section>

  <section class="gallery">
    <div class="photo photo-deck" role="img" aria-label="Photo of a cedar deck with red patio chairs under a pergola, surrounded by trees"></div>
    <div class="photo photo-aerial" role="img" aria-label="Aerial photo of a house with a new paver driveway, walkway and landscaped beds"></div>
    <div class="photo photo-pool" role="img" aria-label="Photo of a modern home with a covered terrace beside a turquoise swimming pool"></div>
    <div class="photo photo-pavilion" role="img" aria-label="Photo of a timber outdoor pavilion with a stacked-stone fireplace and kitchen counters"></div>
  </section>
</main>
</body>
</html>
```